VL - menu design

Hi,

We require elegant menu design for upscale restaurant. Please find attached the logo and the menu items for your reference.

for inspiration, this is a good website: -
http://www.plateworthy-sample.net/dishcraft/about.php

We are very much open for Menu Size suggestions.

unfortunately the place is going under renovation, we don't have updated images to it. the closest look and feel to our place is http://vazelo-example.com ..

we are also open for creative options on the shape, the styles, etc. as long as it represents the fine dine feel ...

Thanks ...

Dear All,

We wouldlike to extend our apology for not being able to provide feedbacks on everysingle design. We were extremely busy and we have multiple contests opensimultaneously which makes the process even harder.

However,we would like to thank you all for the efforts you have put into designingour menu. It is very much appreciated …

We wishyou all success in your design ventures and we are quite positive that we willbe working with many of you on many projects in the soon future. 

Thanks & Regards,

DQI Team...

 

 

 

Industry/Entity Type

Restaurant

Requirements
Must have
• Please ensure that there are 'some' images in the menu ... this is very important.
Should not have
• IMPORTANT: -

1. Please DO NOT insert any currency sign to the menu
2. Please keep the prices of the menu at the end of the menu items descriptions NOT beside the menu item names. The font of the price should be similar to the menu item description and please DO NOT bold the numbers. the prices should be subtle.

Thank you ...

```html
<!DOCTYPE html>
<html lang="en">
<head>
<meta charset="utf-8">
<title>Linden Row Cafe – Menu</title>
<link rel="stylesheet" href="https://fonts.googleapis.com/css2?family=Rajdhani:wght@400;500&family=Crimson+Text:ital,wght@0,600;1,400;1,600&display=swap">
<style>
  :root {
    --backdrop: #1c1c1c;
    --paper: #ffffff;
    --ink: #3a3a3a;
    --heading: #4a4a4a;
    --accent: #8a6a48;
    --rule: #9a9a9a;
    --block: #1e1e1e;
    --sketch-light: #e6dccb;
    --sketch-dark: #b9a88c;
  }
  * { box-sizing: border-box; margin: 0; padding: 0; }
  html, body { width: 1200px; height: 801px; overflow: hidden; background: var(--backdrop); }
  .menu-page {
    position: absolute; left: 180px; top: 15px; width: 840px; height: 770px;
    background: var(--paper); color: var(--ink);
    font-family: "Crimson Text", Georgia, serif;
  }
  .brand-block {
    position: absolute; left: 0; top: 0; width: 247px; height: 140px;
    background: var(--block); display: flex; align-items: center; justify-content: center; gap: 10px;
  }
  .brand-name {
    font-family: "Rajdhani", Arial, sans-serif; font-weight: 500; font-size: 30px;
    letter-spacing: 5px; color: #fff;
  }
  .brand-mark { width: 10px; height: 10px; background: #fff; }
  .sketch {
    position: absolute; border-radius: 50%;
    background: radial-gradient(ellipse at center, var(--sketch-dark) 0%, var(--sketch-light) 55%, rgba(255,255,255,0) 72%);
  }
  .sketch-sandwich { left: 300px; top: 18px; width: 240px; height: 120px; }
  .sketch-vegetables { left: 692px; top: 630px; width: 138px; height: 125px; }
  .section-title {
    font-family: "Rajdhani", Arial, sans-serif; font-weight: 400; font-size: 24px;
    letter-spacing: 1px; color: var(--heading); text-transform: uppercase;
    position: absolute; line-height: 1;
  }
  .rule { position: absolute; background: var(--rule); }
  .rule-h { height: 1px; }
  .rule-v { width: 1px; }
  .column { position: absolute; text-align: center; }
  .dish { margin-bottom: 10px; }
  .dish-name { font-weight: 600; color: var(--accent); font-size: 14px; line-height: 1.1; }
  .dish-desc { font-style: italic; font-size: 9.5px; line-height: 1.25; }
  .breakfast { left: 38px; top: 285px; width: 205px; }
  .sandwiches { left: 285px; top: 240px; width: 540px; }
  .sandwiches .dish { margin-bottom: 6px; }
  .sandwiches .dish-desc { font-size: 10px; }
  .sandwiches .dish-desc b { color: var(--ink); font-weight: 600; }
  .salads { left: 285px; top: 432px; width: 385px; }
  .salads .dish { margin-bottom: 7px; }
  .soup { left: 700px; top: 432px; width: 130px; }
</style>
</head>
<body>
<main class="menu-page">
  <div class="brand-block">
    <span class="brand-mark"></span>
    <span class="brand-name">LINDEN ROW</span>
  </div>
  <div class="sketch sketch-sandwich" role="img" aria-label="Sketch of a stacked sandwich"></div>

  <h2 class="section-title" style="left:300px; top:178px;">The Sandwiches</h2>
  <div class="rule rule-h" style="left:270px; top:207px; width:555px;"></div>
  <h2 class="section-title" style="left:38px; top:236px;">The Breakfast</h2>
  <div class="rule rule-h" style="left:15px; top:265px; width:244px;"></div>
  <div class="rule rule-v" style="left:259px; top:190px; height:560px;"></div>

  <section class="column sandwiches">
    <p class="dish dish-desc"><b>Grilled Vegetables Sandwich</b> with fresh goat cheese and cheese served with our homemade spicy garlic mayo. 59</p>
    <p class="dish dish-desc"><b>Butterfish burger</b> with fresh tomato, beef bacon, grilled vegetables and béarnaise sauce. 79</p>
    <p class="dish dish-desc"><b>Tawuk Tuna sandwich</b> with red onion slices, sliced endives and black olives and sesame pain. 79</p>
    <p class="dish dish-desc"><b>Beef sirloin steak sandwich</b> with grain mustard, Parmesan cheese and fresh rustic pain. 79</p>
    <p class="dish dish-desc"><b>The Traditional Club sandwich</b> served with French fries and vegetable chips. 69</p>
    <p class="dish dish-desc"><b>Chicken sandwich</b> with Parmesan cheese slices, sundried tomatoes and mint flavored mayo. 69</p>
  </section>

  <h2 class="section-title" style="left:300px; top:392px;">Salads</h2>
  <div class="rule rule-h" style="left:270px; top:388px; width:555px;"></div>
  <div class="rule rule-h" style="left:270px; top:420px; width:555px;"></div>
  <h2 class="section-title" style="left:712px; top:392px;">Soup</h2>
  <div class="rule rule-v" style="left:682px; top:388px; height:235px;"></div>

  <section class="column breakfast">
    <div class="dish"><h3 class="dish-name">Butter Croissant</h3><p class="dish-desc">Served plain with a selection of two jams, a vanilla custard cream, a chocolate cream and butter curls. 28</p></div>
    <div class="dish"><h3 class="dish-name">Cheese Croissant</h3><p class="dish-desc">Crumbly freshly baked with cheese filling. 29</p></div>
    <div class="dish"><h3 class="dish-name">Daily Fresh Eggs</h3><p class="dish-desc">A choice of poached, scrambled, pan fried, omelet, all served with toasted bread, mushrooms, roasted tomatoes and chicken sausages. 39</p></div>
    <div class="dish"><h3 class="dish-name">Healthy Time</h3><p class="dish-desc">One choice of hot beverage from our coffee served with fruit salad, natural yoghurt, whole wheat bread vegetable sandwiches and sugar free biscuits selection. 49</p></div>
    <div class="dish"><h3 class="dish-name">Energy Time</h3><p class="dish-desc">One choice of hot beverage from our coffee served with finger chocolate muffins, poached egg with toasted bread and crispy beef bacon, crepe roll with goat cheese and honey and finger chocolate cream with salted cashew. 59</p></div>
    <div class="dish"><h3 class="dish-name">Linden Row Time</h3><p class="dish-desc">One choice of hot beverage from our coffee served with our selection of scones, smoked salmon and avocado sandwich, roasted sausages sandwich, grilled vegetables sandwich, selection of our best breads. 79</p></div>
    <div class="dish"><h3 class="dish-name">The Arabic Breakfast</h3><p class="dish-desc">Choice of Zattar Mhammarah and Cheese Manakish, served with one choice of hot beverage from our coffee and fresh orange juice. 39</p></div>
  </section>

  <section class="column salads">
    <div class="dish"><h3 class="dish-name">Vegetarian Salad</h3><p class="dish-desc">Fresh green leaves, Italian cherry tomatoes, carrots, cucumbers, green apple and toasted pine nuts with our special grain mustard dressing. 59</p></div>
    <div class="dish"><h3 class="dish-name">Sweet Gorgonzola Cheese Salad</h3><p class="dish-desc">Fresh green leaves, Gorgonzola cheese, fresh pears, walnuts, garlic bread croutons, green celery with mustard honey dressing. 59</p></div>
    <div class="dish"><h3 class="dish-name">Beef Sirloin Salad</h3><p class="dish-desc">Fresh green leaves, beef sirloin julienne, caramelized apples, Parmesan cheese, toasted almonds, sundried tomatoes and light pesto sauce. 79</p></div>
    <div class="dish"><h3 class="dish-name">Tandoori Chicken Salad</h3><p class="dish-desc">Fresh green leaves, tandoori chicken breast, fresh mango, fresh goat cheese, crispy chicken skin and fine mint sauce. 69</p></div>
    <div class="dish"><h3 class="dish-name">Seafood Salad</h3><p class="dish-desc">Fresh green leaves, fresh steamed seafood, black olives, celery, garlic bread croutons, avocado and grapefruit dressing. 89</p></div>
    <div class="dish"><h3 class="dish-name">Fresh Tuna Salad</h3><p class="dish-desc">Fresh green leaves, low temperature cooked tuna, niçoise olives, red onions, roasted peppers, soy marinated tofu and lemon dressing. 89</p></div>
  </section>

  <section class="column soup">
    <div class="dish"><h3 class="dish-name">Bouillabaisse</h3><p class="dish-desc">Traditional French seafood soup, with saffron and rouille. 119</p></div>
    <div class="dish"><h3 class="dish-name">Barley soup</h3><p class="dish-desc">With fresh vegetables, tomato smoothie and a hint of garlic oil. 49</p></div>
    <div class="dish"><h3 class="dish-name">Beef chili</h3><p class="dish-desc">Served with Arabic bread, fresh guacamole and spicy black beans. 49</p></div>
  </section>

  <div class="sketch sketch-vegetables" role="img" aria-label="Sketch of mushrooms and garden vegetables"></div>
</main>
</body>
</html>
```